Community coffee table book/quiz book

I need a couple of things for my book:
- Book cover (Title: "1000 spørsmål om Kvernhaugen")
- "Cover pages" for each chapter of the book (15-16 chapters)
- "Watermark" or background design for all the pages of the book.
- A cover image for the book's Kretsbok page.
- Design of a paper "belt"

The book:
The book will consist of about 200+ pages with ten questions on one page and ten answers on the next.

The name of the book is "1000 spørsmål om Kvernhaugen" which means 1000 questions about Fyllingsdalen (Fyllingsdalen is a suburb of the city Bergen in Norway). Author is Helge Myrvold.
The questions in the book are grouped in chapters like:
History
Facts
Schools
Businesses
People/profiles
Sport
Culture
Buildings/Landmarks/Sculptures
The different areas of the suburb
The city
Language/expressions
Nature
The names of the chapters are not set, so it would be good to have the option to change the title of the pages without having to contact the designer (maybe by adding the text on top of the cover page?). I therefore suggest that these images are without text.
The book size is 18X18 cm.

The chapter cover pages:
The book will basically consist of text. Ten questions on one page, and ten questions on the next. Visually it will be quite "boring" to look at. I would therefore like to have a chapter cover page for each chapter, preferable in colour.

Water mark:
To avoid having a book full of white pages with limited amount of text I thought of having some kind of design on each page. I do not know how this should be done, but maybe it is possible to create some kind of background image or watermark image with similar design as the book cover and the chapter covers?

The Kretsbok cover image:
This should be the same as, or similar to, the book cover.
I believe the optimal size is 828px x 315px?

Paper "belt":
The book is to be sold for charity. The receiver of the money is the local sports club. I would like to have the book "wrapped in a 5-6 cm wide paper belt with the logo of the sports club (please see logo and colours here: http://www.ilbrattlia.no). I do not think that the book cover itself should have the sports club's color (purple), but maybe the paper band could? (Again: YOU are the designer)

Photos:
I reckon you would like some photos for both the book cover and the chapter covers. I will of course do the best I can to provide these photos when I have selected a designer. I the meantime

Target Market(s)

Target market is middle clas men and women 35+ from the geographical area Fyllingsdalen.

Industry/Entity Type

Community

Font styles to use
Serif
Sans Serif

Requirements
Must have
• The book will be sold by children on doors. The buyers will probably take a look briefly through the book and then decide if they are going to buy.
• It is important that they like the question types, categories and some of the actual questions they read. But it is also important that they like the look of the book. Therefore the book cover and the chapter cover pages must be appealing enough for the buyers to want this book on theor coffee table.
Nice to have
• I have uploaded a short video clip to Vidtrekk (https://www.vidtrekk.example/watch?v=qx7Ta2Lm9pz). This a promo clip from Pimlo Kanalen. I felt inspired when I saw it and thought that backgrounds like the ones used in the promo could also be used as backgrounds for each chapter's cover pages. Maybe different colour for each chapter? Screenshots from the clip is uploaded below.
• Then again: Maybe I am an idiot? YOU are the designer :-)
Should not have
• There has been some rivalry between two sportsclubs in the region after the clubs was merged a couple of years ago. I therefore believe we should therefore try avoid both the old clubs' colours (blue&yellow and green) and the new club's colour (purple).

```html
<!DOCTYPE html>
<html lang="no">
<head>
<meta charset="utf-8">
<title>Sidebakgrunn – spørsmålsside</title>
<link rel="stylesheet" href="https://fonts.googleapis.com/css2?family=Arimo:wght@700&display=swap">
<style>
  :root {
    --canvas: #ffffff;
    --band-top: #bdbdbd;
    --band-bottom: #b3b3b3;
    --page-light: #f0f0f0;
    --skyline: #e2e2e2;
    --ink: #2b2b2b;
  }
  html, body {
    margin: 0;
    padding: 0;
    overflow: hidden;
    background: var(--canvas);
  }
  .canvas {
    position: relative;
    width: 1200px;
    height: 1000px;
    overflow: hidden;
    background: var(--canvas);
  }
  .page-background {
    position: absolute;
    left: 260px;
    top: 60px;
    width: 740px;
    height: 740px;
  }
  .question-list {
    position: absolute;
    left: 349px;
    top: 171px;
    margin: 0;
    padding: 0;
    list-style: none;
    font-family: "Arimo", Arial, sans-serif;
    font-weight: 700;
    font-size: 25.5px;
    line-height: 52px;
    color: var(--ink);
    white-space: nowrap;
  }
</style>
</head>
<body>
<div class="canvas">
  <svg class="page-background" viewBox="0 0 740 740" width="740" height="740">
    <defs>
      <linearGradient id="skylineFade" x1="0" y1="0" x2="0" y2="1">
        <stop offset="0" stop-color="var(--skyline)" stop-opacity="0.5"/>
        <stop offset="1" stop-color="var(--skyline)" stop-opacity="1"/>
      </linearGradient>
    </defs>
    <rect class="band-top" x="0" y="0" width="740" height="740" fill="var(--band-top)"/>
    <path class="page-light" d="M0 132 C150 40 430 -10 740 50 L740 740 L0 740 Z" fill="var(--page-light)"/>
    <rect class="skyline" x="0" y="480" width="740" height="210" fill="url(#skylineFade)" role="img" aria-label="Svak silhuett av byens bygninger"/>
    <path class="band-bottom" d="M0 692 C260 740 560 720 740 610 L740 740 L0 740 Z" fill="var(--band-bottom)"/>
  </svg>

  <ol class="question-list">
    <li>1. Sakldjs asdlkjsd sahjdsdkh sajsdalhksda</li>
    <li>2. Asjknddfkj dekjhffjh dskjfhsdfjkhdsfjkhskjsd</li>
    <li>3. Qdlkfsjs dslkjfisdfklj sdlkfjdlkfjsdlkfj dksjfldslkj</li>
    <li>4. Bsadlkjdlk sljkdslkdj slkjdklajsdl asdksjd</li>
    <li>5. Lsdkjhga sadhjgasdhui eguwbn jhewvrlskjueh</li>
    <li>6. Wdekjhfs sdkjhffoi edfukiho rouifhoirf</li>
    <li>7. Mfjscfkjds dkjshbiu riugfhrgjnb fdndf;lelruhr</li>
    <li>8. Bsdklfjsofij dihjfiojf id dfij dfj fodfjdofj fddi</li>
    <li>9. Kjdskflkdfsh duhfd hfduhdf difdoiddihd j diud</li>
    <li>10. Gslhjkfd sdufhg fiuf dkjhd du fuhyudhuhyuh</li>
  </ol>
</div>
</body>
</html>
```